Dultavo.com webside

I want to build a Dultavo.com retail website use on Shopify, reselling three main categories: Office Supplies, Packing Supplies, and Home Consumables. I also wish the webpage has the same functions as the Zelvik home page. The page is split into three different parts with the top being a sliding screen showcasing promotion products, below it being the three categories, and finally, a moving screen showing company missions.
Target Market(s)
U.S online
Industry/Entity Type
Office Supplies, packing Supplies and Home Consumables
Coding
Coded - Design and coding required
Number of Pages Required
5+ page
Look and feel

```html
<!DOCTYPE html>
<html lang="en">
<head>
<meta charset="utf-8">
<title>Dultavo — Office, Packing &amp; Home Supplies</title>
<link rel="stylesheet" href="https://fonts.googleapis.com/css2?family=Montserrat:wght@400;500;600;700&family=Roboto+Condensed:wght@400&display=swap">
<style>
:root{
  --teal:#00b9a3;
  --teal-deep:#01a98f;
  --teal-bright:#14dccc;
  --ink:#1b1b1b;
  --muted:#555;
  --line:#e3e3e3;
  --sale-red:#e3141b;
  --white:#fff;
}
*{box-sizing:border-box;margin:0;padding:0}
html,body{width:1200px;height:3795px;overflow:hidden;background:var(--white)}
body{position:relative;font-family:"Montserrat",sans-serif;color:var(--ink)}
.abs{position:absolute}
a{color:inherit;text-decoration:none}

.promo-bar{left:0;top:0;width:1200px;height:40px;background:var(--teal);color:var(--white);
  font-family:"Roboto Condensed",sans-serif;font-size:15px;display:flex;align-items:center;justify-content:center}

.search-icon{left:143px;top:78px}
.brand{left:0;width:1200px;top:64px;text-align:center;font-size:37px;font-weight:500;letter-spacing:.5px}
.cart-icon{left:1037px;top:78px}
.main-nav{left:0;width:1200px;top:141px;display:flex;justify-content:center;gap:39px;font-size:15.5px;font-weight:500}
.main-nav a{padding-bottom:5px}
.main-nav a.active{border-bottom:2px solid var(--teal)}

.hero-photo{left:487px;top:207px;width:568px;height:600px;border-radius:18px;
  background:linear-gradient(160deg,#5a4a3d 0%,#3f342c 45%,#6a5b4f 100%)}
.hero-photo::after{content:"";position:absolute;left:110px;top:0;width:330px;height:440px;border-radius:0 0 16px 16px;
  background:linear-gradient(180deg,#8a8d91,#c9cbce)}
.hero-panel{left:144px;top:297px;width:382px;height:419px;border-radius:18px;background:var(--teal-deep);color:var(--white);padding:52px 38px}
.hero-panel h1{font-size:56px;font-weight:600;line-height:66px;letter-spacing:1px}
.hero-panel p{margin-top:26px;font-size:20.5px;line-height:26.5px}
.shop-btn{display:inline-block;margin-top:24px;background:var(--white);color:var(--teal-deep);font-size:13px;font-weight:700;
  padding:14px 16px;border-radius:24px}

.section-title{left:144px;top:900px;font-size:31px;font-weight:700;letter-spacing:.5px}

.product-card{top:986px;width:209px;height:282px;background:var(--white);box-shadow:0 1px 6px rgba(0,0,0,.22);text-align:center}
.product-card .thumb{margin:10px;height:193px;position:relative}
.product-card h3{margin-top:15px;font-size:17px;font-weight:600}
.price{font-size:12px;margin-top:8px}
.price s{color:var(--muted);margin-right:6px}
.price span{color:var(--teal-deep)}
.sale-pill{position:absolute;left:6px;top:9px;background:var(--teal-deep);color:var(--white);font-size:11px;font-weight:700;padding:4px 12px;border-radius:12px}

.quote-band{left:0;top:1350px;width:1200px;height:253px;background:linear-gradient(180deg,var(--teal-deep),var(--teal-bright));color:var(--white);text-align:center}
.quote-band blockquote{margin:58px auto 0;width:740px;font-size:22.5px;font-weight:600;line-height:29.5px}
.quote-band cite{display:block;margin-top:24px;font-style:normal;font-size:13.5px;font-weight:700;letter-spacing:.5px}

.cat-card{background:var(--white);box-shadow:0 1px 7px rgba(0,0,0,.25);text-align:center}
.cat-card .thumb{margin:14px;position:relative}
.cat-card h3{font-size:23px;font-weight:600}
.cat-card .price{font-size:16px;margin-top:14px}
.sale-tag{position:absolute;left:16px;bottom:14px;background:var(--sale-red);color:var(--white);font-size:16px;font-weight:700;padding:4px 14px}

.feature{top:2510px;width:230px;text-align:center}
.feature svg{display:block;margin:0 auto}
.feature h4{margin-top:28px;font-size:13.5px;font-weight:600;letter-spacing:.4px}
.feature p{margin-top:8px;font-family:Arial,sans-serif;font-size:11px;color:var(--muted);line-height:18px}

.blog-card{top:2743px;width:285px;height:381px}
.blog-card .thumb{height:261px}
.blog-card h3{margin-top:28px;font-size:22px;line-height:28px;font-weight:600}

.footer-zone{left:0;top:3211px;width:1200px;height:584px;background:linear-gradient(180deg,#8fdccb 0%,#4cc7b0 50%,#1fb39a 100%);color:var(--white)}
.footer-zone h2{position:absolute;top:82px;width:1200px;text-align:center;font-size:31px;font-weight:700;letter-spacing:1px}
.footer-zone .sub{position:absolute;top:137px;width:1200px;text-align:center;font-size:17.5px}
.email-field{position:absolute;left:399px;top:194px;width:402px;height:51px;background:var(--white);color:#555;font-size:13.5px;display:flex;align-items:center;justify-content:space-between;padding:0 22px}
.foot-col{position:absolute;top:308px}
.foot-col h5{font-size:22px;font-weight:700;letter-spacing:.5px}
.foot-col ul{list-style:none;margin-top:10px}
.foot-col li{font-size:17px;line-height:26.5px}
.social{display:flex;gap:22px;margin-top:14px;font-size:11px;font-weight:600}
.social div{text-align:center}
.social span.dot{display:block;width:28px;height:28px;border-radius:50%;background:var(--white);margin:0 auto 4px}
.legal{position:absolute;left:144px;top:517px;font-size:13px}
.contact-mail{position:absolute;right:145px;top:512px;font-size:18px;font-weight:600;display:flex;align-items:center;gap:12px}
</style>
</head>
<body>

<div class="abs promo-bar">Buy One, Get One 50% off.</div>

<svg class="abs search-icon" width="20" height="20" viewBox="0 0 20 20" aria-label="Search"><circle cx="8" cy="8" r="6" fill="none" stroke="#111" stroke-width="2.6"/><line x1="12.5" y1="12.5" x2="18" y2="18" stroke="#111" stroke-width="2.8"/></svg>
<div class="abs brand">Dultavo</div>
<svg class="abs cart-icon" width="16" height="16" viewBox="0 0 16 16" aria-label="Cart"><path d="M2 4h12l-1 10H3z" fill="none" stroke="#555" stroke-width="1.2"/><path d="M5.5 6V3.5a2.5 2.5 0 0 1 5 0V6" fill="none" stroke="#555" stroke-width="1.2"/></svg>

<nav class="abs main-nav">
  <a class="active" href="#">Home</a><a href="#">About Us</a><a href="#">Products</a><a href="#">Blog</a><a href="#">Categories</a><a href="#">Contact Us</a>
</nav>

<div class="abs hero-photo" role="img" aria-label="Laptop, tablet, notebook and mouse on a wooden desk"></div>
<section class="abs hero-panel">
  <h1>OFFICE SUPPLIES</h1>
  <p>At vero eos et accusamus et iusto odio dignissimos ducii blanditiispraesentiumvoluptat ulpa qui officia um</p>
  <a class="shop-btn" href="#">SHOP NOW</a>
</section>

<h2 class="abs section-title">SHOP OUR MOST TRUSTED PRODUCTS</h2>

<article class="abs product-card" style="left:144px">
  <div class="thumb" role="img" aria-label="Cardboard box with packing tape" style="background:linear-gradient(135deg,#eeeeee,#d9cdbd)"><span class="sale-pill">SALE</span></div>
  <h3>Excepteur sint</h3><p class="price"><s>$19.00 CAD</s><span>$16.00 CAD</span></p>
</article>
<article class="abs product-card" style="left:378px">
  <div class="thumb" role="img" aria-label="Colourful pens, folders and stationery" style="background:linear-gradient(135deg,#f4f4f4,#d9a0c8 50%,#8fc6e2)"></div>
  <h3>Nemo enim ipsam</h3><p class="price"><s>$19.00 CAD</s><span>$16.00 CAD</span></p>
</article>
<article class="abs product-card" style="left:612px">
  <div class="thumb" role="img" aria-label="Green and yellow cleaning sponge" style="background:linear-gradient(135deg,#f0f0f0 30%,#1f6a45 60%,#eeeeee)"><span class="sale-pill">SALE</span></div>
  <h3>Neque porrsquam</h3><p class="price"><s>$19.00 CAD</s><span>$16.00 CAD</span></p>
</article>
<article class="abs product-card" style="left:845px">
  <div class="thumb" role="img" aria-label="Open box filled with office supplies" style="background:linear-gradient(135deg,#eeeeee,#b88a5e 60%,#eeeeee)"></div>
  <h3>Quis autem vel</h3><p class="price"><s>$19.00 CAD</s><span>$16.00 CAD</span></p>
</article>

<section class="abs quote-band">
  <blockquote>“Lorem ipsum dolor sit amet, consectetur adipiscing elit, sed do eiusmod tempor incididunt ut labore et dolore magna aliqua. Quis ipsum suspendisse ultrices gravida”</blockquote>
  <cite>CORABEL, FOUNDER</cite>
</section>

<article class="abs cat-card" style="left:144px;top:1636px;width:283px;height:381px">
  <div class="thumb" role="img" aria-label="White desk with keyboard, notebook and plant" style="height:261px;background:linear-gradient(135deg,#d8d8d8,#ededed 60%,#c9c9c9)"></div>
  <h3>Office Supplies</h3><p class="price"><s>$19.00 CAD</s><span>$16.00 CAD</span></p>
</article>
<article class="abs cat-card" style="left:144px;top:2038px;width:283px;height:380px">
  <div class="thumb" role="img" aria-label="Stacked cardboard boxes and tape dispenser" style="height:261px;background:linear-gradient(135deg,#8c6c4c,#c7a882 55%,#a9896a)"></div>
  <h3>Packing Supplies</h3><p class="price"><s>$19.00 CAD</s><span>$16.00 CAD</span></p>
</article>
<article class="abs cat-card" style="left:452px;top:1636px;width:602px;height:782px">
  <div class="thumb" role="img" aria-label="Blue bucket with cleaning bottles, brush and cloth" style="height:662px;background:linear-gradient(160deg,#dcdcdc 0%,#c9c6c1 40%,#2fb3e0 70%,#b8a68e 100%)"><span class="sale-tag">SALE</span></div>
  <h3>Home Consumables</h3><p class="price"><s>$19.00 CAD</s><span>$16.00 CAD</span></p>
</article>

<div class="abs feature" style="left:121px">
  <svg width="48" height="32" viewBox="0 0 48 32" aria-hidden="true" fill="none" stroke="#14a88f" stroke-width="2"><rect x="10" y="6" width="22" height="18"/><path d="M32 12h8l5 6v6H32"/><circle cx="16" cy="26" r="3"/><circle cx="38" cy="26" r="3"/><path d="M2 10h6M0 15h8M3 20h5"/></svg>
  <h4>FREE SHIPPING</h4><p>Nemo enim ipsam vollg hluptatem<br>quia voluptas sit aut odit</p>
</div>
<div class="abs feature" style="left:364px">
  <svg width="40" height="42" viewBox="0 0 40 42" aria-hidden="true" fill="none" stroke="#14a88f" stroke-width="2"><circle cx="20" cy="14" r="9"/><path d="M4 40c2-10 8-14 16-14s14 4 16 14z"/><path d="M10 14c0-8 20-8 20 0"/></svg>
  <h4>CUSTOMER SERVICE</h4><p>Nemo enim ipsam vollg hluptatem<br>quia voluptas sit aut odit</p>
</div>
<div class="abs feature" style="left:605px">
  <svg width="40" height="40" viewBox="0 0 40 40" aria-hidden="true" fill="none" stroke="#14a88f" stroke-width="2"><circle cx="20" cy="16" r="8"/><path d="M20 11v10M17 13h5M18 19h5"/><path d="M8 30c6-4 18-4 24 0v6H8z"/><path d="M4 10l3 2M36 10l-3 2M20 2v4"/></svg>
  <h4>MONEY BACK GUARANTEE</h4><p>Nemo enim ipsam vollg hluptatem<br>quia voluptas sit aut odit</p>
</div>
<div class="abs feature" style="left:848px">
  <svg width="42" height="34" viewBox="0 0 42 34" aria-hidden="true" fill="none" stroke="#14a88f" stroke-width="2"><rect x="10" y="12" width="28" height="18" rx="2" fill="#14a88f" fill-opacity=".15"/><path d="M10 18h28"/><path d="M4 14l20-10 6 8"/><rect x="26" y="22" width="8" height="4"/></svg>
  <h4>SAFE PAYMENT</h4><p>Nemo enim ipsam vollg hluptatem<br>quia voluptas sit aut odit</p>
</div>

<article class="abs cat-card blog-card" style="left:144px">
  <div class="thumb" role="img" aria-label="Warehouse shelves with boxes on a conveyor" style="background:linear-gradient(180deg,#6a7580,#9aa3ab 50%,#c49a64 75%,#7a93b0)"></div>
  <h3>Excepteur sint<br>occaecat cupidatat</h3>
</article>
<article class="abs cat-card blog-card" style="left:458px">
  <div class="thumb" role="img" aria-label="Notepads and binder clips on grey surface" style="background:linear-gradient(135deg,#b9bec4,#d3d7db 50%,#aeb3b9)"></div>
  <h3>Sed ut perspiciatis<br>unde omnis iste</h3>
</article>
<article class="abs cat-card blog-card" style="left:770px">
  <div class="thumb" role="img" aria-label="Cleaning products, gloves and sponges in a basket" style="background:linear-gradient(180deg,#d9d9d9,#c7c7c7 45%,#e77fa9 70%,#9c6f4a)"></div>
  <h3>Nemo enim ipsam<br>voluptassi</h3>
</article>

<footer class="abs footer-zone">
  <h2>GET 20% OFF YOUR FIRST ORDER</h2>
  <p class="sub">Join our email list for exclusive offers and the latest news.</p>
  <div class="email-field"><span>Enter Email</span>
    <svg width="26" height="14" viewBox="0 0 26 14" aria-hidden="true"><path d="M0 7h24M18 1l6 6-6 6" fill="none" stroke="#333" stroke-width="1.6"/></svg></div>

  <div class="foot-col" style="left:237px"><h5>MENU</h5>
    <ul><li>Home</li><li>About Us</li><li>Products</li><li>Blog</li></ul></div>
  <div class="foot-col" style="left:512px"><h5>OTHER LINKS</h5>
    <ul><li>Contact us</li><li>Shipping</li><li>Returns</li><li>Payment</li></ul></div>
  <div class="foot-col" style="left:864px"><h5>FIND US</h5>
    <div class="social"><div><span class="dot"></span>Circlebook</div><div><span class="dot"></span>Pictaly</div></div></div>

  <p class="legal">© 2022.dultavo.All Rights Reserved &nbsp;| Privacy &nbsp;| &nbsp;Terms and Conditions</p>
  <p class="contact-mail"><svg width="20" height="15" viewBox="0 0 20 15" aria-hidden="true"><rect width="20" height="15" rx="2" fill="#fff"/><path d="M1 2l9 7 9-7" fill="none" stroke="#1fb39a" stroke-width="1.6"/></svg>Email : info@dultavo.com</p>
</footer>

</body>
</html>
```